electronics flyer required for small business

We need a flyer designed to advertise the services that our company Vorla-Electronics can provide. These services include installation or repair of phone systems, door intercoms / access controls, CCTV, Security systems, mobile phone signal boosting, digital TV services, network systems and sockets , basically anything electronics we can look at doing. We would like them to call us if they have any electronics based enquires. Free no obligation quote provided

Target Market(s)

small business

Industry/Entity Type

Small Business

Requirements
Must have
• contact details
• 01638405912
• 07481326970
• enquiries@vorla-systems.net
Nice to have
• memorable and eye catching

```html
<!DOCTYPE html>
<html lang="en">
<head>
<meta charset="utf-8">
<title>Vorla-Electronics – Services Flyer</title>
<link rel="stylesheet" href="https://fonts.googleapis.com/css2?family=PT+Sans:wght@400;700&family=Open+Sans:wght@700;800&display=swap">
<style>
  :root {
    --backdrop: #d8c6a6;
    --paper: #ffffff;
    --brand-blue: #0b6fb8;
    --strip-blue: #5fc3ef;
    --ring-blue: #79cdf2;
    --heading-blue: #1e6fb6;
    --ink: #1f1f1f;
    --teal: #2c8e98;
    --teal-light: #4fb0b6;
    --white: #ffffff;
  }
  html, body {
    margin: 0;
    padding: 0;
    width: 944px;
    height: 1200px;
    overflow: hidden;
    background: var(--backdrop);
  }
  .canvas {
    position: relative;
    width: 944px;
    height: 1200px;
  }
  .flyer {
    position: absolute;
    left: 82px;
    top: 52px;
    width: 774px;
    height: 1094px;
    background: var(--paper);
    overflow: hidden;
    font-family: "PT Sans", Arial, sans-serif;
  }
  .header-band {
    position: absolute;
    left: 0; top: 0;
    width: 774px; height: 96px;
    background: var(--brand-blue);
  }
  .brand-name {
    position: absolute;
    left: 0; top: 40px;
    width: 774px;
    margin: 0;
    text-align: center;
    font-family: "Open Sans", Arial, sans-serif;
    font-weight: 800;
    font-size: 58px;
    line-height: 1;
    color: var(--white);
    letter-spacing: 1px;
  }
  .side-strip {
    position: absolute;
    left: 78px; top: 96px;
    width: 36px; height: 912px;
    background: var(--strip-blue);
  }
  .photo-ring {
    position: absolute;
    left: 32px;
    width: 236px; height: 236px;
    border-radius: 50%;
    border: 9px solid var(--ring-blue);
    box-sizing: border-box;
    background: var(--white);
    overflow: hidden;
  }
  .photo-ring .photo {
    width: 100%; height: 100%;
  }
  .ring-phones { top: 130px; }
  .ring-phones .photo { background: linear-gradient(135deg, #f0f0f0 0%, #9a9ea3 55%, #3a3d42 100%); }
  .ring-intercom { top: 340px; }
  .ring-intercom .photo { background: linear-gradient(160deg, #c9ccd0 0%, #8d9298 50%, #e6e8ea 100%); }
  .ring-camera { top: 548px; }
  .ring-camera .photo { background: linear-gradient(150deg, #e3e3e3 0%, #a7a7a7 55%, #5c5c5c 100%); }
  .ring-alarm { top: 760px; }
  .ring-alarm .photo { background: linear-gradient(140deg, #e4e6e4 0%, #b9bcb8 55%, #8d918c 100%); }
  .circuit-photo {
    position: absolute;
    left: 248px; top: 108px;
    width: 512px; height: 372px;
    background: radial-gradient(ellipse at 55% 45%, #6f8fb3 0%, #9fb5cc 45%, #d9e3ee 75%, #ffffff 100%);
  }
  .services {
    position: absolute;
    left: 280px; top: 510px;
  }
  .services-heading {
    display: flex;
    align-items: center;
    margin: 0;
    font-size: 30px;
    font-weight: 400;
    color: var(--heading-blue);
  }
  .services-heading svg { margin-right: 12px; }
  .service-list {
    list-style: none;
    margin: 12px 0 0 0;
    padding: 0;
    font-size: 21px;
    color: var(--ink);
  }
  .service-list li {
    height: 35.5px;
    line-height: 35.5px;
  }
  .service-list li::before {
    content: "»";
    margin-right: 4px;
  }
  .call-to-action {
    position: absolute;
    left: 310px; top: 870px;
    width: 280px; height: 140px;
    color: var(--heading-blue);
    font-family: "PT Sans", Arial, sans-serif;
  }
  .cta-initial {
    position: absolute;
    left: 0; top: -12px;
    font-size: 150px;
    line-height: 1;
  }
  .cta-rest {
    position: absolute;
    left: 54px; top: 0;
    font-size: 68px;
    line-height: 1;
  }
  .cta-line2 {
    position: absolute;
    left: 48px; top: 62px;
    font-size: 68px;
    line-height: 1;
  }
  .cta-line2 .dark { color: var(--ink); }
  .quote-note {
    position: absolute;
    left: 576px; top: 866px;
    width: 134px; height: 124px;
    background: linear-gradient(160deg, var(--teal-light), var(--teal));
    transform: rotate(-16deg);
    box-shadow: 3px 4px 8px rgba(0,0,0,0.3);
    display: flex;
    align-items: center;
    justify-content: center;
    text-align: center;
    font-family: "Open Sans", Arial, sans-serif;
    font-weight: 700;
    font-size: 17px;
    line-height: 1.2;
    color: var(--white);
  }
  .contact-band {
    position: absolute;
    left: 0; top: 1008px;
    width: 774px; height: 86px;
    background: var(--brand-blue);
    color: var(--white);
  }
  .contact-band .phone-icon {
    position: absolute;
    left: 26px; top: 14px;
  }
  .phone-numbers {
    position: absolute;
    left: 113px; top: 12px;
    font-weight: 700;
    font-size: 26px;
    line-height: 32px;
  }
  .email {
    position: absolute;
    right: 22px; top: 28px;
    font-weight: 700;
    font-size: 22px;
  }
</style>
</head>
<body>
<div class="canvas">
  <section class="flyer">
    <div class="header-band"></div>
    <div class="side-strip"></div>

    <div class="circuit-photo" role="img" aria-label="Close-up photo of a circuit board being soldered"></div>

    <h1 class="brand-name">Vorla-Electronics</h1>

    <div class="photo-ring ring-phones"><div class="photo" role="img" aria-label="Photo of an office phone system with desk handsets"></div></div>
    <div class="photo-ring ring-intercom"><div class="photo" role="img" aria-label="Photo of a video door intercom screen and door panel"></div></div>
    <div class="photo-ring ring-camera"><div class="photo" role="img" aria-label="Photo of a wall-mounted CCTV camera"></div></div>
    <div class="photo-ring ring-alarm"><div class="photo" role="img" aria-label="Photo of a hand pressing a security alarm keypad"></div></div>

    <div class="services">
      <h2 class="services-heading">
        <svg width="44" height="44" viewBox="0 0 44 44" aria-hidden="true">
          <circle cx="22" cy="22" r="22" fill="var(--brand-blue)"/>
          <polyline points="17,12 28,22 17,32" fill="none" stroke="#fff" stroke-width="3.5" stroke-linecap="round" stroke-linejoin="round"/>
        </svg>
        Services:
      </h2>
      <ul class="service-list">
        <li>Installation Or Repair Of Phone Systems</li>
        <li>Door Intercoms / Access Controls</li>
        <li>CCTV</li>
        <li>Security Systems</li>
        <li>Mobile Phone Signal Boosting</li>
        <li>Digital Tv Services</li>
        <li>Network Systems And Sockets</li>
        <li>Basically Anything Electronics</li>
      </ul>
    </div>

    <div class="call-to-action" aria-label="Just call us">
      <span class="cta-initial">J</span>
      <span class="cta-rest">ust</span>
      <span class="cta-line2"><span class="dark">call</span>Us..</span>
    </div>

    <div class="quote-note">FREE NO<br>OBLIGATION<br>QUOTE</div>

    <footer class="contact-band">
      <svg class="phone-icon" width="70" height="58" viewBox="0 0 70 58" aria-hidden="true">
        <path d="M4 20 C4 6 66 6 66 20 L66 26 L50 26 L50 18 L20 18 L20 26 L4 26 Z" fill="#fff"/>
        <path d="M18 24 L52 24 L62 50 C62 54 60 56 56 56 L14 56 C10 56 8 54 8 50 Z" fill="#fff"/>
        <circle cx="35" cy="40" r="10" fill="var(--brand-blue)"/>
        <circle cx="35" cy="40" r="5" fill="#fff"/>
      </svg>
      <div class="phone-numbers">01638405912<br>07481326970</div>
      <div class="email">enquiries@vorla-systems.net</div>
    </footer>
  </section>
</div>
</body>
</html>
```